Website for software company "velora"

We need a website for our software company/startup named "velora". We are developing several products (currently 3 standard-software products) which are all in different sectors, but all our products are available for Laptops/PC/Mobile Phones/Tablets, ... We do also create custom software and support our customers with consulting to optimize their processes.
We already have a Logo which you can find in the attached files.
We are a young team of 4 members (two founders and 2 employees).

To get an idea of our products -> the first one is a planning software for healthcare organizations (eg. BlueHaven, firebrigade, pharmacy), the second one is a booking software for sport clubs and the third one is a competition software for sports hunting. You see very diverse. Include or ignore this info of our products as you like.

The design has to be a bootstrap 4 (or higher) design. We have licenced FontAwesome as iconset. Responsive design should come without saying.

• Starting page, product pages, news section, contact, team, services

```html
<!DOCTYPE html>
<html lang="en">
<head>
<meta charset="utf-8">
<title>velora — Website Pages</title>
<link href="https://fonts.googleapis.com/css2?family=Poppins:wght@400;500;600;700&display=swap" rel="stylesheet">
<style>
:root{
  --orange:#f47b20;
  --orange-soft:#fde9da;
  --peach:#fdf1e8;
  --ink:#262b33;
  --ink-2:#3a3f47;
  --muted:#7b7f86;
  --line:#e7e7e7;
  --paper:#ffffff;
  --mist:#f3f3f4;
  --stage:#e9e9ea;
}
*{margin:0;padding:0;box-sizing:border-box}
html,body{width:816px;height:1200px;overflow:hidden}
body{background:var(--stage);font-family:'Poppins',sans-serif;color:var(--ink);position:relative}
svg text{font-family:'Poppins',sans-serif}
.page{position:absolute;width:505px;background:var(--paper);transform:scale(0.624);transform-origin:0 0;overflow:hidden;box-shadow:0 10px 30px rgba(0,0,0,.12)}
.page--home{left:73px;top:10px;height:1892px}
.page--products{left:428px;top:137px;height:1480px}
.page > *{position:absolute}
.bg{left:0;top:0;width:505px}
.blob{border-radius:50%;background:var(--peach)}

.brand{font-weight:600;color:var(--ink);letter-spacing:.5px;display:flex;align-items:center;gap:5px;line-height:1}
.brand-mark{width:.7em;height:.7em;background:var(--orange);display:inline-block}
.nav{display:flex;gap:11px;font-size:5px;font-weight:500;color:var(--ink-2);letter-spacing:.2px}
.nav span{position:relative}
.nav .active{color:var(--orange)}
.nav .active::before{content:"";position:absolute;left:0;right:0;top:-9px;height:1.5px;background:var(--orange)}
.btn-pill{border:1px solid var(--ink);border-radius:10px;font-size:5px;font-weight:600;display:flex;align-items:center;justify-content:center}
.btn-orange{background:var(--orange);color:#fff;border-radius:10px;font-size:5px;font-weight:600;display:flex;align-items:center;justify-content:center;letter-spacing:.2px}

.h-sec{font-size:14px;font-weight:600;text-align:center;width:505px;left:0}
.lead{font-size:6px;line-height:1.6;color:var(--muted)}
.h-prod{font-size:11px;font-weight:600;line-height:1.35}
.para{font-size:5.4px;line-height:1.75;color:var(--muted)}
.link{font-size:5px;font-weight:600;color:var(--orange);text-decoration:underline;letter-spacing:.2px}
.on-orange{color:#fff}

.hero-art{background:
  radial-gradient(circle at 70% 40%,rgba(244,123,32,.35),rgba(244,123,32,0) 38%),
  radial-gradient(circle at 42% 70%,rgba(38,43,51,.55),rgba(38,43,51,0) 34%),
  radial-gradient(circle at 82% 62%,rgba(38,43,51,.35),rgba(38,43,51,0) 30%),
  linear-gradient(135deg,#f7f7f8,#eceef1);border-radius:50% 40% 30% 45%/40% 45% 35% 40%}
.ui{display:block}
.shadow{filter:drop-shadow(0 5px 10px rgba(0,0,0,.1))}

.card{background:#fff;border-radius:4px;box-shadow:0 4px 16px rgba(0,0,0,.08)}
.service{display:flex;flex-direction:column;align-items:center;text-align:center;padding:22px 12px 0}
.service svg{width:36px;height:36px;margin-bottom:8px}
.service h4{font-size:5.6px;font-weight:600;line-height:1.5;margin-bottom:7px}
.service p{font-size:5px;line-height:1.7;color:var(--muted)}

.team{padding:3px}
.team .photo{height:78px;border-radius:2px}
.team h5{font-size:6px;font-weight:600;text-align:center;margin-top:9px}
.team small{display:block;font-size:4.6px;color:var(--muted);text-align:center;margin-top:1px}

.news{padding:3px}
.news .photo{height:84px;border-radius:2px}
.news time{display:block;font-size:4.6px;color:var(--muted);margin:8px 7px 2px}
.news h5{font-size:6px;font-weight:600;line-height:1.35;margin:0 7px 5px}
.news p{font-size:4.8px;line-height:1.6;color:var(--muted);margin:0 7px}

.footer-col h6{font-size:7px;font-weight:600;color:#fff;margin-bottom:8px}
.footer-col li{list-style:none;font-size:5px;color:#c3c6cb;line-height:13px}
.footer-col li::before{content:"› ";color:#8b9097}
.contact-row{display:flex;gap:5px;font-size:5px;color:#c3c6cb;line-height:1.45;margin-bottom:8px}
.contact-row svg{width:6px;height:6px;flex:none;margin-top:1px}
.socials{display:flex;gap:5px}
.socials i{width:13px;height:13px;border-radius:50%;background:#3a4049;display:block}
.rule{height:1px;background:#3d434c}
.copy{font-size:5px;font-weight:600;color:#fff;text-align:center;width:505px;left:0}
.to-top{width:16px;height:16px;border-radius:50%;background:var(--orange);display:flex;align-items:center;justify-content:center}

.feature{display:flex;align-items:center;gap:6px;font-size:5.4px;font-weight:600;color:#fff;line-height:1.45}
.feature svg{width:19px;height:19px;flex:none}
.feature--left{justify-content:flex-end;text-align:right}
.hire-circle{width:108px;height:108px;border-radius:50%;background:#fff;display:flex;align-items:center;justify-content:center}
.hire-circle .brand{font-size:20px;color:var(--orange)}

.steps{width:175px}
.steps li{list-style:none;display:flex;justify-content:space-between;font-size:5.6px;font-weight:500;border-bottom:1px solid var(--line);padding:6px 0 8px}
.steps li b{color:var(--orange);font-weight:500}
.hire{display:flex;flex-direction:column;align-items:center;padding-top:14px;text-align:center}
.hire svg{width:30px;height:30px;margin-bottom:10px}
.hire h4{font-size:5.6px;font-weight:600;line-height:1.45}
.faq{width:330px}
.faq li{list-style:none;display:flex;justify-content:space-between;font-size:5.8px;font-weight:500;border-bottom:1px solid var(--line);padding:6px 0 9px}
.faq li b{color:var(--orange);font-weight:500}
</style>
</head>
<body>

<svg width="0" height="0" style="position:absolute" aria-hidden="true">
  <defs>
    <linearGradient id="bannerTone" x1="0" x2="1"><stop offset="0" stop-color="#6d7179"/><stop offset="1" stop-color="#8d9097"/></linearGradient>
    <symbol id="health-dashboard" viewBox="0 0 258 158">
      <rect x=".5" y=".5" width="257" height="157" rx="5" fill="#fff" stroke="#2b3038"/>
      <rect x="1" y="1" width="16" height="156" fill="#fafafa"/>
      <rect x="5" y="6" width="7" height="7" rx="1.5" fill="#3b5bdb"/>
      <rect x="5" y="36" width="7" height="7" rx="2" fill="var(--orange)"/>
      <g fill="#d5d7db"><circle cx="8.5" cy="54" r="1.6"/><circle cx="8.5" cy="66" r="1.6"/><circle cx="8.5" cy="78" r="1.6"/><circle cx="8.5" cy="90" r="1.6"/><circle cx="8.5" cy="102" r="1.6"/></g>
      <text x="26" y="12" font-size="5" font-weight="600" fill="#262b33">Dashboard</text>
      <rect x="26" y="20" width="146" height="30" rx="3" fill="url(#bannerTone)"/>
      <text x="31" y="29" font-size="3" font-weight="600" fill="#fff">Find using your clinic account</text>
      <text x="31" y="34" font-size="2.4" fill="#e6e6e6">Get all your visits in one simple place</text>
      <rect x="31" y="40" width="20" height="5" rx="1" fill="#fff"/>
      <rect x="140" y="22" width="26" height="28" rx="2" fill="#9a9ca2" role="img" aria-label="Doctor at a desk"/>
      <g>
        <rect x="26" y="56" width="46" height="40" rx="2" fill="#fff" stroke="#eceef1"/>
        <text x="30" y="63" font-size="2.6" fill="#7b7f86">All visits</text><text x="55" y="66" font-size="4.5" font-weight="600" fill="#262b33">214</text>
        <path d="M28 84 C36 78,40 90,48 82 S62 80,70 86 L70 94 L28 94Z" fill="#dde9fb"/><path d="M28 84 C36 78,40 90,48 82 S62 80,70 86" fill="none" stroke="#6c9ce8" stroke-width=".8"/>
        <rect x="76" y="56" width="46" height="40" rx="2" fill="#fff" stroke="#eceef1"/>
        <text x="80" y="63" font-size="2.6" fill="#7b7f86">New patients</text><text x="105" y="66" font-size="4.5" font-weight="600" fill="#262b33">148</text>
        <path d="M78 86 C86 80,92 92,100 84 S112 78,120 84 L120 94 L78 94Z" fill="#e6ecf9"/><path d="M78 86 C86 80,92 92,100 84 S112 78,120 84" fill="none" stroke="#8ea6dc" stroke-width=".8"/>
        <rect x="126" y="56" width="46" height="40" rx="2" fill="#fff" stroke="#eceef1"/>
        <text x="130" y="63" font-size="2.6" fill="#7b7f86">Cancelled visits</text><text x="158" y="66" font-size="4.5" font-weight="600" fill="#262b33">27</text>
        <path d="M128 82 C136 90,142 78,150 86 S162 76,170 84 L170 94 L128 94Z" fill="#fbe1e4"/><path d="M128 82 C136 90,142 78,150 86 S162 76,170 84" fill="none" stroke="#e98a95" stroke-width=".8"/>
      </g>
      <text x="26" y="106" font-size="3" font-weight="600" fill="#262b33">Notifications</text>
      <g fill="#eef0f3">
        <rect x="26" y="111" width="146" height="8" rx="1"/><rect x="26" y="122" width="146" height="8" rx="1"/><rect x="26" y="133" width="146" height="8" rx="1"/><rect x="26" y="144" width="146" height="8" rx="1"/>
      </g>
      <g fill="#b5b8be"><rect x="30" y="114" width="60" height="2"/><rect x="30" y="125" width="52" height="2"/><rect x="30" y="136" width="64" height="2"/><rect x="30" y="147" width="48" height="2"/></g>
      <g><rect x="118" y="113" width="14" height="4" rx="1" fill="#fde2cf"/><rect x="118" y="124" width="14" height="4" rx="1" fill="#e8dcf7"/><rect x="118" y="135" width="14" height="4" rx="1" fill="#fde2cf"/><rect x="118" y="146" width="14" height="4" rx="1" fill="#dde9fb"/></g>
      <line x1="178" y1="4" x2="178" y2="154" stroke="#eceef1"/>
      <text x="184" y="12" font-size="3" font-weight="600" fill="#262b33">Upcoming visits</text>
      <g fill="#f1f2f4"><rect x="184" y="18" width="8" height="10" rx="1.5"/><rect x="195" y="18" width="8" height="10" rx="1.5"/><rect x="217" y="18" width="8" height="10" rx="1.5"/><rect x="228" y="18" width="8" height="10" rx="1.5"/><rect x="239" y="18" width="8" height="10" rx="1.5"/></g>
      <rect x="206" y="18" width="8" height="10" rx="1.5" fill="#262b33"/>
      <g>
        <circle cx="188" cy="40" r="3" fill="#e3e6ea"/><rect x="194" y="38" width="28" height="2" fill="#7b7f86"/><rect x="194" y="42" width="40" height="1.6" fill="#c8cbd0"/>
        <circle cx="188" cy="56" r="3" fill="#e3e6ea"/><rect x="194" y="54" width="24" height="2" fill="#7b7f86"/><rect x="194" y="58" width="36" height="1.6" fill="#c8cbd0"/>
        <circle cx="188" cy="72" r="3" fill="#e3e6ea"/><rect x="194" y="70" width="30" height="2" fill="#7b7f86"/><rect x="194" y="74" width="34" height="1.6" fill="#c8cbd0"/>
        <circle cx="188" cy="104" r="3" fill="#e3e6ea"/><rect x="194" y="102" width="26" height="2" fill="#7b7f86"/><rect x="194" y="106" width="38" height="1.6" fill="#c8cbd0"/>
        <circle cx="188" cy="120" r="3" fill="#e3e6ea"/><rect x="194" y="118" width="30" height="2" fill="#7b7f86"/><rect x="194" y="122" width="32" height="1.6" fill="#c8cbd0"/>
        <circle cx="188" cy="136" r="3" fill="#e3e6ea"/><rect x="194" y="134" width="22" height="2" fill="#7b7f86"/><rect x="194" y="138" width="36" height="1.6" fill="#c8cbd0"/>
      </g>
    </symbol>
  </defs>
</svg>

<!-- Home page -->
<section class="page page--home" aria-label="velora home page">
  <svg class="bg" height="1892" viewBox="0 0 505 1892" aria-hidden="true">
    <polygon points="0,310 505,230 505,480 0,480" fill="#f4f4f5"/>
    <polygon points="0,767 505,830 505,968 0,968" fill="var(--orange)"/>
    <polygon points="0,1740 505,1640 505,1662 0,1760" fill="#ececee"/>
    <polygon points="0,1759 505,1660 505,1892 0,1892" fill="var(--ink)"/>
  </svg>
  <div class="blob" style="left:-20px;top:530px;width:140px;height:140px"></div>
  <div class="blob" style="left:410px;top:700px;width:140px;height:140px"></div>
  <div class="blob" style="left:-30px;top:1025px;width:130px;height:130px"></div>
  <div class="blob" style="left:420px;top:1255px;width:120px;height:120px"></div>

  <div class="brand" style="left:37px;top:12px;font-size:18px"><i class="brand-mark"></i>velora</div>
  <nav class="nav" style="left:201px;top:17px"><span class="active">HOME</span><span>OUR PRODUCT</span><span>OUR SERVICES</span><span>OUR TEAM</span><span>LATEST NEWS</span></nav>
  <div class="btn-pill" style="left:413px;top:10px;width:54px;height:18px">CONTACT</div>

  <h1 style="left:37px;top:82px;font-size:28px;font-weight:600;line-height:1.12">We are<br>Developing<br>Products</h1>
  <p class="lead" style="left:37px;top:182px;width:160px">Our products are available for Laptops/PC Mobile Phones/Tablets, ...</p>
  <div class="btn-orange" style="left:37px;top:212px;width:72px;height:18px">START FREE TRIAL</div>
  <div class="hero-art" role="img" aria-label="Illustration of a developer at a large monitor beside a phone showing code, in orange and dark tones" style="left:215px;top:62px;width:268px;height:176px"></div>

  <h2 class="h-sec" style="top:304px">Our Services</h2>
  <div class="card service" style="left:72px;top:334px;width:115px;height:136px">
    <svg viewBox="0 0 36 36" fill="none" stroke="var(--ink)" stroke-width="1.3"><rect x="4" y="6" width="28" height="19" rx="1.5"/><path d="M14 30h8M18 25v5M14 13l-3 3 3 3M22 13l3 3-3 3M19.5 12l-3 8"/></svg>
    <h4>Developing standard<br>software product</h4>
    <p>Lorem quis bibendum auctor, nisi elit consequat ipsum nec sagittis sem nibh elit.</p>
  </div>
  <div class="card service" style="left:195px;top:334px;width:115px;height:136px">
    <svg viewBox="0 0 36 36" fill="none" stroke="var(--ink)" stroke-width="1.3"><circle cx="18" cy="14" r="6"/><path d="M10 14a8 8 0 0 1 16 0M9 13v4M27 13v4M27 17c0 3-3 5-7 5M7 33c1-6 5-9 11-9s10 3 11 9"/></svg>
    <h4>Customer support<br>and consulting</h4>
    <p>Lorem quis bibendum auctor, nisi elit consequat ipsum nec sagittis sem nibh elit.</p>
  </div>
  <div class="card service" style="left:318px;top:334px;width:115px;height:136px">
    <svg viewBox="0 0 36 36" fill="none" stroke="var(--ink)" stroke-width="1.3"><rect x="12" y="5" width="21" height="15" rx="1"/><path d="M20 24h6M23 20v4"/><rect x="3" y="14" width="9" height="16" rx="1.5"/><rect x="14" y="23" width="6" height="9" rx="1"/></svg>
    <h4>Products for Laptops/PC<br>Mobile Phones/Tablets</h4>
    <p>Lorem quis bibendum auctor, nisi elit consequat ipsum nec sagittis sem nibh elit.</p>
  </div>

  <h2 class="h-sec" style="top:505px">Our Products</h2>
  <p class="lead" style="left:105px;top:528px;width:295px;text-align:center;font-size:5.4px">Our products are available for Laptops/PC/Mobile Phones/Tablets, ... We do also create custom software and support our customers with consulting to optimize their processes.</p>

  <svg class="ui shadow" style="left:40px;top:580px" width="258" height="158" role="img" aria-label="Healthcare planning dashboard"><use href="#health-dashboard"/></svg>
  <svg class="ui shadow" style="left:24px;top:726px" width="64" height="18" viewBox="0 0 64 18" aria-hidden="true"><rect width="64" height="18" rx="2" fill="#fff"/><rect x="4" y="3" width="12" height="4" rx="1" fill="#9aa0a8"/><text x="4" y="13" font-size="3" fill="#262b33">Patient Mira Kowal cancelled visit</text></svg>
  <svg class="ui shadow" style="left:230px;top:680px" width="46" height="16" viewBox="0 0 46 16" aria-hidden="true"><rect width="46" height="16" rx="2" fill="#fff"/><rect x="3" y="4" width="8" height="8" rx="1.5" fill="var(--orange)"/><rect x="14" y="5" width="18" height="2" fill="#7b7f86"/><rect x="14" y="9" width="26" height="1.6" fill="#c8cbd0"/></svg>
  <h3 class="h-prod" style="left:331px;top:609px;width:150px">Software for healthcare organizations</h3>
  <p class="para" style="left:331px;top:643px;width:130px">Aenean sollicitudin, lorem quis bibendum auctor, nisi elit consequat ipsum, nec sagittis sem nibh id elit duis sed odio sit amet nibh vulputate...</p>
  <span class="link" style="left:331px;top:692px">VIEW PRODUCT</span>

  <h3 class="h-prod on-orange" style="left:37px;top:834px;width:130px">Booking software for sport clubs</h3>
  <p class="para on-orange" style="left:37px;top:868px;width:130px">Aenean sollicitudin, lorem quis bibendum auctor, nisi elit consequat ipsum, nec sagittis sem nibh id elit duis sed odio sit amet nibh vulputate...</p>
  <span class="link on-orange" style="left:37px;top:917px">VIEW PRODUCT</span>

  <div class="card" style="left:268px;top:768px;width:92px;height:102px">
    <svg width="92" height="102" viewBox="0 0 92 102" aria-label="September calendar" role="img">
      <rect x="6" y="6" width="7" height="7" rx="1" fill="none" stroke="#ccc" stroke-width=".5"/><rect x="79" y="6" width="7" height="7" rx="1" fill="none" stroke="#ccc" stroke-width=".5"/>
      <text x="46" y="11.5" font-size="4.4" font-weight="600" text-anchor="middle" fill="#262b33">September 2019</text>
      <g font-size="3" fill="#9a9ea5" text-anchor="middle"><text x="10" y="22">Sun</text><text x="22" y="22">Mon</text><text x="34" y="22">Tue</text><text x="46" y="22">Wed</text><text x="58" y="22">Thu</text><text x="70" y="22">Fri</text><text x="82" y="22">Sat</text></g>
      <circle cx="70" cy="69" r="3.8" fill="#3a3f47"/>
      <g font-size="3.2" fill="#3a3f47" text-anchor="middle">
        <text x="10" y="31">28</text><text x="22" y="31">29</text><text x="34" y="31">30</text><text x="46" y="31">1</text><text x="58" y="31">2</text><text x="70" y="31">3</text><text x="82" y="31">4</text>
        <text x="10" y="41">5</text><text x="22" y="41">6</text><text x="34" y="41">7</text><text x="46" y="41">8</text><text x="58" y="41">9</text><text x="70" y="41">10</text><text x="82" y="41">11</text>
        <text x="10" y="51">12</text><text x="22" y="51">13</text><text x="34" y="51">14</text><text x="46" y="51">15</text><text x="58" y="51">16</text><text x="70" y="51">17</text><text x="82" y="51">18</text>
        <text x="10" y="60">19</text><text x="22" y="60">20</text><text x="34" y="60">21</text><text x="46" y="60">22</text><text x="58" y="60">23</text><text x="82" y="60">24</text>
        <text x="10" y="70">25</text><text x="22" y="70">26</text><text x="34" y="70">27</text><text x="46" y="70">28</text><text x="58" y="70">29</text><text x="70" y="70" fill="#fff">30</text><text x="82" y="70">1</text>
        <text x="10" y="80">2</text><text x="22" y="80">3</text><text x="34" y="80">4</text><text x="46" y="80">5</text><text x="58" y="80">6</text><text x="70" y="80">7</text><text x="82" y="80">8</text>
      </g>
      <rect x="8" y="88" width="16" height="7" rx="1.5" fill="none" stroke="#d5d7db" stroke-width=".5"/><text x="16" y="92.8" font-size="2.8" text-anchor="middle" fill="#7b7f86">Clear</text>
      <rect x="66" y="88" width="18" height="7" rx="1.5" fill="var(--orange-soft)"/><text x="75" y="92.8" font-size="2.8" text-anchor="middle" fill="var(--orange)">OK</text>
    </svg>
  </div>
  <div class="card" style="left:237px;top:880px;width:115px;height:138px;padding:8px">
    <div style="font-size:7px;font-weight:600;line-height:1.3">Discover spaces for<br>Meetings</div>
    <div style="font-size:3.6px;color:var(--muted);margin-top:4px">Book premium room at low prices instantly</div>
    <svg width="99" height="90" viewBox="0 0 99 90" style="display:block;margin-top:6px" aria-label="Room search form" role="img">
      <g fill="none" stroke="#dfe1e5" stroke-width=".6">
        <rect x=".5" y=".5" width="98" height="11" rx="1.5"/>
        <rect x=".5" y="17.5" width="47" height="11" rx="1.5"/><rect x="51.5" y="17.5" width="47" height="11" rx="1.5"/>
        <rect x=".5" y="34.5" width="47" height="11" rx="1.5"/><rect x="51.5" y="34.5" width="47" height="11" rx="1.5"/>
      </g>
      <g font-size="3.4" fill="#3a3f47"><text x="5" y="7.5">Select Location</text><text x="5" y="24.5">19/9/2019</text><text x="56" y="24.5">Time</text><text x="5" y="41.5">Duration</text><text x="56" y="41.5">Capacity</text></g>
      <path d="M91 5l2 2 2-2" fill="none" stroke="#3a3f47" stroke-width=".6"/>
      <rect x="0" y="52" width="28" height="11" rx="1.5" fill="#5a6069"/><text x="14" y="58.8" font-size="3.2" text-anchor="middle" fill="#fff">Find Room</text>
    </svg>
  </div>
  <div class="card" style="left:373px;top:832px;width:93px;height:158px;padding:4px">
    <div role="img" aria-label="Sports event poster with athletes in motion" style="height:64px;border-radius:2px;background:radial-gradient(circle at 45% 55%,#e4552a 0,#f08a45 30%,rgba(253,226,203,0) 60%),linear-gradient(160deg,#fde2cb,#f9c9a0)"></div>
    <div style="font-size:5px;font-weight:600;margin:6px 3px 0">Harbor Row Towers</div>
    <div style="font-size:3.6px;color:var(--muted);margin:2px 3px 0">Harbor Road, Central District, Eastland</div>
    <svg width="85" height="36" viewBox="0 0 85 36" style="display:block;margin:5px 0 0 0" aria-hidden="true">
      <g fill="none" stroke="#9a9ea5" stroke-width=".6"><circle cx="6" cy="4" r="2.4"/><rect x="14" y="2" width="5" height="4"/><circle cx="28" cy="4" r="2.4"/><rect x="36" y="2" width="5" height="4"/><circle cx="50" cy="4" r="2.4"/><rect x="58" y="2" width="5" height="4"/></g>
      <g fill="#f2f2f3"><rect x="2" y="14" width="25" height="18" rx="1.5"/><rect x="30" y="14" width="25" height="18" rx="1.5"/><rect x="58" y="14" width="25" height="18" rx="1.5"/></g>
      <g font-size="2.6" fill="#9a9ea5"><text x="4" y="20">Per hour</text><text x="32" y="20">Per half day</text><text x="60" y="20">Per full day</text></g>
      <g font-size="3.6" font-weight="600" fill="#3a3f47"><text x="4" y="28">$22</text><text x="32" y="28">$40</text><text x="60" y="28">$53</text></g>
    </svg>
    <div class="btn-orange" style="margin:6px auto 0;width:56px;height:11px;background:var(--orange-soft);color:var(--orange);border-radius:2px">Book Now</div>
  </div>
  <div class="card" style="left:206px;top:872px;width:18px;height:18px"></div>
  <div class="card" style="left:375px;top:800px;width:16px;height:16px"></div>

  <!-- hunting phones -->
  <svg class="ui shadow" style="left:38px;top:1080px" width="75" height="165" viewBox="0 0 75 165" role="img" aria-label="Hunting app home screen">
    <rect x=".5" y=".5" width="74" height="164" rx="7" fill="#fff" stroke="#dfe2e8"/>
    <text x="6" y="20" font-size="5" font-weight="600" fill="#262b33">Let's Hunting</text>
    <rect x="6" y="26" width="63" height="7" rx="1.5" fill="#f1f2f4"/>
    <g fill="#eef0f3"><rect x="6" y="38" width="14" height="5" rx="1"/><rect x="23" y="38" width="14" height="5" rx="1"/><rect x="40" y="38" width="14" height="5" rx="1"/></g>
    <rect x="6" y="48" width="50" height="40" rx="2" fill="#c9a77a" role="img" aria-label="Hunters on a ridge at dusk"/>
    <rect x="6" y="48" width="50" height="40" rx="2" fill="url(#dusk)"/>
    <defs><linearGradient id="dusk" x1="0" y1="0" x2="0" y2="1"><stop offset="0" stop-color="#e9e3d6"/><stop offset=".6" stop-color="#c9b89a"/><stop offset="1" stop-color="#3a3f47"/></linearGradient></defs>
    <rect x="6" y="92" width="26" height="2.2" fill="#3a3f47"/><rect x="6" y="97" width="18" height="1.6" fill="#c8cbd0"/>
    <rect x="6" y="104" width="50" height="7" rx="1.5" fill="#f1f2f4"/>
    <line x1="0" y1="150" x2="75" y2="150" stroke="#eee"/>
    <g fill="#d5d7db"><circle cx="12" cy="157" r="2"/><circle cx="25" cy="157" r="2"/><circle cx="51" cy="157" r="2"/><circle cx="63" cy="157" r="2"/></g><circle cx="38" cy="157" r="3" fill="#3a3f47"/>
  </svg>
  <svg class="ui shadow" style="left:126px;top:1042px" width="73" height="165" viewBox="0 0 73 165" role="img" aria-label="Hunting app detail screen with savanna landscape">
    <defs><linearGradient id="savanna" x1="0" y1="0" x2="0" y2="1"><stop offset="0" stop-color="#c9d6df"/><stop offset=".45" stop-color="#d9b07a"/><stop offset="1" stop-color="#b9873e"/></linearGradient></defs>
    <rect x=".5" y=".5" width="72" height="164" rx="7" fill="#fff" stroke="#dfe2e8"/>
    <path d="M.5 8a7.5 7.5 0 0 1 7.5-7.5h57a7.5 7.5 0 0 1 7.5 7.5V110H.5z" fill="url(#savanna)"/>
    <text x="5" y="72" font-size="5" font-weight="600" fill="#fff">Moragore</text>
    <rect x="5" y="84" width="8" height="8" rx="1.5" fill="var(--orange)"/>
    <rect x="52" y="100" width="18" height="14" rx="2" fill="#e9d5b3"/>
    <rect x="5" y="118" width="30" height="2.2" fill="#3a3f47"/><rect x="5" y="124" width="40" height="1.6" fill="#c8cbd0"/>
    <circle cx="50" cy="134" r="8" fill="none" stroke="#d5d7db" stroke-width=".6"/>
    <rect x="40" y="152" width="28" height="7" rx="1" fill="#3a3f47"/>
  </svg>
  <svg class="ui shadow" style="left:212px;top:1080px" width="73" height="165" viewBox="0 0 73 165" role="img" aria-label="Hunting app map and night hunting screen">
    <defs><linearGradient id="night" x1="0" y1="0" x2="0" y2="1"><stop offset="0" stop-color="#f1ece3"/><stop offset="1" stop-color="#8a8278"/></linearGradient></defs>
    <rect x=".5" y=".5" width="72" height="164" rx="7" fill="#fff" stroke="#dfe2e8"/>
    <rect x="4" y="12" width="65" height="70" rx="2" fill="#f6f6f7"/>
    <path d="M10 70 C25 40,40 60,60 22" fill="none" stroke="#d5d7db" stroke-dasharray="2 2" stroke-width=".6"/>
    <circle cx="40" cy="26" r="3" fill="var(--orange)"/><circle cx="16" cy="50" r="2" fill="#c8cbd0"/><circle cx="60" cy="58" r="2" fill="#c8cbd0"/>
    <rect x="4" y="88" width="65" height="40" rx="2" fill="url(#night)"/>
    <text x="36.5" y="112" font-size="5.4" font-weight="600" text-anchor="middle" fill="#262b33">Night Hunting</text>
    <rect x="6" y="133" width="26" height="2" fill="#3a3f47"/><rect x="6" y="138" width="18" height="1.6" fill="#c8cbd0"/>
    <rect x="6" y="150" width="61" height="8" rx="1" fill="#4a5058"/>
  </svg>
  <h3 class="h-prod" style="left:331px;top:1099px;width:150px">Sports hunting you see very diverse</h3>
  <p class="para" style="left:331px;top:1133px;width:130px">Aenean sollicitudin, lorem quis bibendum auctor, nisi elit consequat ipsum, nec sagittis sem nibh id elit duis sed odio sit amet nibh vulputate...</p>
  <span class="link" style="left:331px;top:1182px">VIEW PRODUCT</span>

  <h2 class="h-sec" style="top:1282px">velora Team</h2>
  <div class="card team" style="left:60px;top:1315px;width:88px;height:112px"><div class="photo" role="img" aria-label="Portrait of Theo Marsh in a tan blazer" style="background:linear-gradient(180deg,#eef0f2 0,#e6dccf 55%,#b79a78 100%)"></div><h5>Theo Marsh</h5><small>Founder</small></div>
  <div class="card team" style="left:159px;top:1315px;width:88px;height:112px"><div class="photo" role="img" aria-label="Portrait of Lena Ortiz in a denim jacket" style="background:linear-gradient(180deg,#eef0f2 0,#e3d3c6 50%,#3f5068 100%)"></div><h5>Lena Ortiz</h5><small>Employee</small></div>
  <div class="card team" style="left:258px;top:1315px;width:88px;height:112px"><div class="photo" role="img" aria-label="Portrait of Ravi Kessler in a light shirt" style="background:linear-gradient(180deg,#eef0f2 0,#e8c9a8 50%,#f4f4f4 100%)"></div><h5>Ravi Kessler</h5><small>Founder</small></div>
  <div class="card team" style="left:357px;top:1315px;width:88px;height:112px"><div class="photo" role="img" aria-label="Portrait of Omar Bennett in a denim shirt" style="background:linear-gradient(180deg,#eef0f2 0,#8a6a55 50%,#6f8fb0 100%)"></div><h5>Omar Bennett</h5><small>Employee</small></div>

  <h2 style="left:37px;top:1527px;font-size:14px;font-weight:600">Latest News</h2>
  <p class="para" style="left:37px;top:1550px;width:130px">Aenean sollicitudin, lorem quis bibendum auctor, nisi elit consequat ipsum, nec sagittis sem nibh id elit duis sed odio sit amet nibh vulputate...</p>
  <article class="card news" style="left:190px;top:1478px;width:110px;height:154px"><div class="photo" role="img" aria-label="Illustration of a person coding at a desk" style="background:radial-gradient(circle at 50% 60%,#3c6fd8 0,#7fb0e6 30%,rgba(207,230,245,0) 55%),linear-gradient(160deg,#dbeefa,#a9d2ef)"></div><time>25-02-2022</time><h5>Some event heading goes here</h5><p>Aenean sollicitudin lorem bibendum auctor nisi elit consequat ipsum...</p></article>
  <article class="card news" style="left:313px;top:1478px;width:110px;height:154px"><div class="photo" role="img" aria-label="Illustration of a person working at a laptop" style="background:radial-gradient(circle at 50% 60%,#9b59d0 0,#e58ac6 30%,rgba(251,217,238,0) 55%),linear-gradient(160deg,#fde3f2,#f5bfe0)"></div><time>25-02-2022</time><h5>Some event heading goes here</h5><p>Aenean sollicitudin lorem bibendum auctor nisi elit consequat ipsum...</p></article>
  <article class="card news" style="left:436px;top:1478px;width:110px;height:154px"><div class="photo" role="img" aria-label="Illustration of people at a workstation" style="background:radial-gradient(circle at 50% 60%,#5a5fd0 0,#a6a8ea 30%,rgba(226,224,248,0) 55%),linear-gradient(160deg,#ebe9fb,#cdc9f1)"></div><time>25-02-2022</time><h5>Some event heading goes here</h5><p>Aenean sollicitudin lorem bibendum auctor nisi elit consequat ipsum...</p></article>

  <div class="brand" style="left:66px;top:1780px;font-size:22px;color:#fff"><i class="brand-mark"></i>velora</div>
  <div class="socials" style="left:80px;top:1814px"><i></i><i></i><i></i><i></i></div>
  <div class="footer-col" style="left:195px;top:1752px"><h6>Quick Links</h6><ul><li>Home</li><li>Our Product</li><li>Our Services</li><li>Our Team</li><li>Latest news</li><li>Contact Us</li></ul></div>
  <div class="footer-col" style="left:278px;top:1752px"><h6>Information</h6><ul><li>Privacy Policy</li><li>Terms &amp; Conditions</li><li>Shipping Policy</li><li>FAQ's</li><li>Sitemap</li><li>Blog</li></ul></div>
  <div class="footer-col" style="left:366px;top:1752px"><h6>Contact info</h6>
    <div class="contact-row"><svg viewBox="0 0 8 8"><rect x=".5" y="1.5" width="7" height="5" fill="var(--orange)"/></svg><span>Email:<br>info@velora.io</span></div>
    <div class="contact-row"><svg viewBox="0 0 8 8"><path d="M1 1.5l2-.8 1 2-1 .8a4 4 0 0 0 1.6 1.6l.8-1 2 1-.8 2C3.5 7 1 4.5 1 1.5z" fill="var(--orange)"/></svg><span>Phone:<br>08 555-014-2210</span></div>
    <div class="contact-row"><svg viewBox="0 0 8 8"><path d="M4 .5a2.6 2.6 0 0 1 2.6 2.6C6.6 5 4 7.5 4 7.5S1.4 5 1.4 3.1A2.6 2.6 0 0 1 4 .5z" fill="var(--orange)"/></svg><span>Location:<br>Some address line goes<br>here city name country</span></div>
  </div>
  <div class="rule" style="left:37px;top:1866px;width:430px"></div>
  <p class="copy" style="top:1877px">© Copyright 2022 velora, All Rights Reserved</p>
  <div class="to-top" style="left:477px;top:1859px"><svg width="6" height="6" viewBox="0 0 6 6"><path d="M3 5V1M1 3l2-2 2 2" stroke="#fff" fill="none" stroke-width=".8"/></svg></div>
</section>

<!-- Products page -->
<section class="page page--products" aria-label="velora products page">
  <svg class="bg" height="1480" viewBox="0 0 505 1480" aria-hidden="true">
    <polygon points="0,382 505,290 505,555 0,555" fill="var(--orange)"/>
    <polygon points="0,835 505,770 505,1030 0,1030" fill="#f4f4f5"/>
    <polygon points="0,1328 505,1243 505,1268 0,1346" fill="#ececee"/>
    <polygon points="0,1346 505,1268 505,1480 0,1480" fill="var(--ink)"/>
  </svg>
  <div class="blob" style="left:5px;top:95px;width:130px;height:130px"></div>
  <div class="blob" style="left:385px;top:720px;width:130px;height:130px"></div>

  <div class="brand" style="left:37px;top:12px;font-size:18px"><i class="brand-mark"></i>velora</div>
  <nav class="nav" style="left:201px;top:17px"><span>HOME</span><span class="active">OUR PRODUCT</span><span>OUR SERVICES</span><span>OUR TEAM</span><span>LATEST NEWS</span></nav>
  <div class="btn-pill" style="left:417px;top:10px;width:54px;height:18px">CONTACT</div>

  <h1 class="h-sec" style="top:54px;font-size:23px">Our Products</h1>
  <p class="lead" style="left:0;top:88px;width:505px;text-align:center;font-size:6px">Our products are available for Laptops/PC Mobile Phones/Tablets, ...</p>

  <svg class="ui shadow" style="left:35px;top:138px" width="243" height="149" viewBox="0 0 258 158" role="img" aria-label="Healthcare planning dashboard"><use href="#health-dashboard"/></svg>
  <svg class="ui shadow" style="left:18px;top:278px" width="100" height="24" viewBox="0 0 100 24" aria-hidden="true"><rect width="100" height="24" rx="2" fill="#fff"/><rect x="6" y="4" width="14" height="5" rx="1" fill="#9aa0a8"/><text x="72" y="8" font-size="3" fill="#7b7f86">21 May, 10:27</text><text x="6" y="17" font-size="3.4" fill="#262b33">Patient Mira Kowal cancelled visit at 11:30</text></svg>
  <h3 class="h-prod" style="left:314px;top:139px;width:170px;font-size:12.5px">Software for healthcare organizations</h3>
  <p class="para" style="left:314px;top:177px;width:165px">Lorem ipsum dolor sit amet, consectetur adipiscing elit. Aenean sodales dictum viverra. Nam gravida dignissim eros. Vivamus congue erat ante, volutpat dictum neque dignissim eget. Aenean sollicitudin, lorem quis bibendum auctor, nisi elit consequat ipsum, nec sagittis sem nibh id elit duis sed odio sit amet nibh vulputate...</p>
  <div class="btn-orange" style="left:314px;top:258px;width:82px;height:18px">DISCUS YOUR PROJECT</div>

  <h2 class="h-sec on-orange" style="top:368px;font-size:12.5px;line-height:1.35">Hire Web Design<br>and Development Experts</h2>
  <div class="hire-circle" style="left:193px;top:416px"><div class="brand">velora</div></div>
  <div class="feature feature--left" style="left:60px;top:425px;width:120px"><span>Prototyping &amp; UI/UX<br>Designing</span><svg viewBox="0 0 20 20" fill="none" stroke="#fff" stroke-width="1"><path d="M2 18L18 2M2 18h16M2 18V2"/><path d="M6 14l3-3M9 17V14"/></svg></div>
  <div class="feature feature--left" style="left:60px;top:460px;width:120px"><span>Progressive Web<br>Development</span><svg viewBox="0 0 20 20" fill="none" stroke="#fff" stroke-width="1"><rect x="2" y="3" width="16" height="14" rx="1"/><path d="M2 7h16"/><circle cx="10" cy="12" r="2.5"/></svg></div>
  <div class="feature feature--left" style="left:60px;top:495px;width:120px"><span>Custom Website<br>Development</span><svg viewBox="0 0 20 20" fill="none" stroke="#fff" stroke-width="1"><rect x="2" y="3" width="16" height="14" rx="1"/><path d="M7 8l-2 2 2 2M13 8l2 2-2 2M11 7l-2 6"/></svg></div>
  <div class="feature" style="left:314px;top:425px;width:120px"><svg viewBox="0 0 20 20" fill="none" stroke="#fff" stroke-width="1"><path d="M10 2l8 4-8 4-8-4zM2 10l8 4 8-4M2 14l8 4 8-4"/></svg><span>Full Stack<br>Development</span></div>
  <div class="feature" style="left:314px;top:460px;width:120px"><svg viewBox="0 0 20 20" fill="none" stroke="#fff" stroke-width="1"><rect x="2" y="3" width="16" height="14" rx="1"/><path d="M6 13l1.5-5 1.5 5M6.5 11.5h2M11 13V8h1.5a1.3 1.3 0 0 1 0 2.6H11M15 8v5"/></svg><span>API<br>Development</span></div>
  <div class="feature" style="left:314px;top:495px;width:120px"><svg viewBox="0 0 20 20" fill="none" stroke="#fff" stroke-width="1"><rect x="3" y="2" width="10" height="16" rx="1"/><path d="M15 6v8M13 10h5M6 14h4"/></svg><span>Upgradation and<br>Migration</span></div>

  <h2 style="left:37px;top:587px;font-size:12.5px;font-weight:600;line-height:1.3;width:190px">How Web Development Outsourcing With velora Works?</h2>
  <ul class="steps" style="left:37px;top:646px">
    <li>Discuss Your Requirements<b>+</b></li>
    <li>Get a Proposal<b>+</b></li>
    <li>Web Development and Designing<b>+</b></li>
    <li>Quality Assurance<b>+</b></li>
    <li>Project Launch<b>+</b></li>
  </ul>
  <svg class="ui shadow" style="left:243px;top:595px" width="224" height="160" viewBox="0 0 224 160" role="img" aria-label="Clinic dashboard with doctor profile, calendar and patient table">
    <defs><linearGradient id="docTone" x1="0" y1="0" x2="0" y2="1"><stop offset="0" stop-color="#eceef1"/><stop offset=".5" stop-color="#e3c7ad"/><stop offset="1" stop-color="#f8f8f8"/></linearGradient></defs>
    <rect x=".5" y=".5" width="223" height="159" rx="5" fill="#fff" stroke="#e4e6ea"/>
    <path d="M5 .5h9v159H5a4.5 4.5 0 0 1-4.5-4.5V5A4.5 4.5 0 0 1 5 .5z" fill="#2b3038"/>
    <g fill="#6b7079"><circle cx="7.5" cy="8" r="2.5"/><rect x="5" y="24" width="5" height="3"/><rect x="5" y="34" width="5" height="3"/><rect x="5" y="54" width="5" height="3"/><rect x="5" y="64" width="5" height="3"/><rect x="5" y="144" width="5" height="3"/></g>
    <rect x="4" y="43" width="7" height="6" rx="1" fill="#fff"/>
    <rect x="20" y="6" width="40" height="5" rx="1" fill="#f1f2f4"/>
    <rect x="24" y="20" width="22" height="28" rx="2" fill="url(#docTone)" role="img" aria-label="Doctor portrait"/>
    <text x="52" y="25" font-size="3.4" font-weight="600" fill="#262b33">Dr. Elias Varn</text>
    <g fill="#fde2cf"><rect x="52" y="30" width="9" height="3" rx="1"/><rect x="63" y="30" width="9" height="3" rx="1"/><rect x="74" y="30" width="9" height="3" rx="1"/></g>
    <g fill="#d5d7db"><rect x="52" y="37" width="80" height="1.4"/><rect x="52" y="40" width="74" height="1.4"/><rect x="52" y="43" width="66" height="1.4"/></g>
    <g><rect x="24" y="56" width="28" height="10" rx="1.5" fill="#f6f6f7"/><rect x="56" y="56" width="28" height="10" rx="1.5" fill="#f6f6f7"/><rect x="88" y="56" width="28" height="10" rx="1.5" fill="#f6f6f7"/><rect x="120" y="56" width="28" height="10" rx="1.5" fill="#f6f6f7"/></g>
    <g font-size="3.4" font-weight="600" fill="#262b33"><text x="33" y="63">1,250</text><text x="65" y="63">250</text><text x="97" y="63">180</text><text x="129" y="63">120</text></g>
    <text x="24" y="76" font-size="3" font-weight="600" fill="#262b33">Last Patients Data</text>
    <g fill="#b5b8be">
      <rect x="24" y="81" width="8" height="1.5"/><rect x="40" y="81" width="18" height="1.5"/><rect x="66" y="81" width="22" height="1.5"/><rect x="96" y="81" width="14" height="1.5"/><rect x="118" y="81" width="18" height="1.5"/>
      <rect x="24" y="88" width="8" height="1.5"/><rect x="40" y="88" width="18" height="1.5"/><rect x="66" y="88" width="22" height="1.5"/><rect x="96" y="88" width="14" height="1.5"/><rect x="118" y="88" width="18" height="1.5"/>
      <rect x="24" y="95" width="8" height="1.5"/><rect x="40" y="95" width="18" height="1.5"/><rect x="66" y="95" width="22" height="1.5"/><rect x="96" y="95" width="14" height="1.5"/><rect x="118" y="95" width="18" height="1.5"/>
      <rect x="24" y="102" width="8" height="1.5"/><rect x="40" y="102" width="18" height="1.5"/><rect x="66" y="102" width="22" height="1.5"/><rect x="96" y="102" width="14" height="1.5"/><rect x="118" y="102" width="18" height="1.5"/>
      <rect x="24" y="109" width="8" height="1.5"/><rect x="40" y="109" width="18" height="1.5"/><rect x="66" y="109" width="22" height="1.5"/><rect x="96" y="109" width="14" height="1.5"/><rect x="118" y="109" width="18" height="1.5"/>
    </g>
    <line x1="155" y1="16" x2="155" y2="154" stroke="#eceef1"/>
    <text x="160" y="24" font-size="3.2" font-weight="600" fill="#262b33">December 2021</text>
    <g fill="#d5d7db">
      <rect x="160" y="30" width="56" height="1.2"/>
      <rect x="160" y="36" width="56" height="1.2"/><rect x="160" y="42" width="56" height="1.2"/><rect x="160" y="48" width="56" height="1.2"/><rect x="160" y="54" width="56" height="1.2"/><rect x="160" y="60" width="56" height="1.2"/>
    </g>
    <circle cx="184" cy="48.6" r="2.6" fill="#262b33"/>
    <g><rect x="160" y="76" width="58" height="12" rx="2" fill="#f6f6f7"/><rect x="160" y="92" width="58" height="12" rx="2" fill="#2b3038"/><rect x="160" y="108" width="58" height="12" rx="2" fill="#f6f6f7"/></g>
    <g fill="#9a9ea5"><rect x="166" y="80" width="24" height="1.6"/><rect x="166" y="112" width="24" height="1.6"/></g><rect x="166" y="96" width="24" height="1.6" fill="#fff"/>
    <rect x="160" y="130" width="14" height="5" rx="1" fill="#f1f2f4"/><rect x="198" y="130" width="14" height="5" rx="1" fill="#f1f2f4"/>
  </svg>

  <h2 class="h-sec" style="top:858px;font-size:12.5px">Hire Dedicated Web Developers</h2>
  <p style="left:0;top:880px;width:505px;text-align:center;font-size:6px;font-weight:600">Choose How You Want to Collaborate</p>
  <div class="card hire" style="left:65px;top:905px;width:91px;height:90px"><svg viewBox="0 0 30 30" fill="none" stroke="var(--orange)" stroke-width="1.1"><rect x="6" y="3" width="18" height="24" rx="1"/><path d="M10 9h10M10 13h10M10 22l3-4 3 2 4-5"/></svg><h4>Project-Based</h4></div>
  <div class="card hire" style="left:160px;top:905px;width:91px;height:90px"><svg viewBox="0 0 30 30" fill="none" stroke="var(--orange)" stroke-width="1.1"><circle cx="15" cy="15" r="12"/><path d="M15 8v7l5 3"/></svg><h4>Hire Developers on<br>Hourly Basis</h4></div>
  <div class="card hire" style="left:255px;top:905px;width:91px;height:90px"><svg viewBox="0 0 30 30" fill="none" stroke="var(--orange)" stroke-width="1.1"><circle cx="15" cy="10" r="3.5"/><circle cx="7" cy="12" r="3"/><circle cx="23" cy="12" r="3"/><path d="M8 24c0-4 3-7 7-7s7 3 7 7M1 23c0-3 2-5 5-5M29 23c0-3-2-5-5-5"/></svg><h4>Dedicated Team<br>of Developers</h4></div>
  <div class="card hire" style="left:350px;top:905px;width:91px;height:90px"><svg viewBox="0 0 30 30" fill="none" stroke="var(--orange)" stroke-width="1.1"><circle cx="15" cy="15" r="12"/><path d="M11.5 12a3.5 3.5 0 1 1 5 3c-1 .6-1.5 1.3-1.5 2.5M15 21v.5"/></svg><h4>I'm not sure</h4></div>

  <h2 class="h-sec" style="top:1063px;font-size:12.5px">Frequently Asked Questions</h2>
  <ul class="faq" style="left:88px;top:1098px">
    <li>1. What's the difference between website design and development?<b>+</b></li>
    <li>2. What is included in website development?<b>+</b></li>
    <li>3. What programming languages do web developers use?<b>+</b></li>
    <li>4. How much does building a website typically cost?<b>+</b></li>
    <li>5. What's the difference between website design and development?<b>+</b></li>
  </ul>

  <div class="brand" style="left:66px;top:1366px;font-size:22px;color:#fff"><i class="brand-mark"></i>velora</div>
  <div class="socials" style="left:80px;top:1400px"><i></i><i></i><i></i><i></i></div>
  <div class="footer-col" style="left:195px;top:1338px"><h6>Quick Links</h6><ul><li>Home</li><li>Our Product</li><li>Our Services</li><li>Our Team</li><li>Latest news</li><li>Contact Us</li></ul></div>
  <div class="footer-col" style="left:278px;top:1338px"><h6>Information</h6><ul><li>Privacy Policy</li><li>Terms &amp; Conditions</li><li>Shipping Policy</li><li>FAQ's</li><li>Sitemap</li><li>Blog</li></ul></div>
  <div class="footer-col" style="left:366px;top:1338px"><h6>Contact info</h6>
    <div class="contact-row"><svg viewBox="0 0 8 8"><rect x=".5" y="1.5" width="7" height="5" fill="var(--orange)"/></svg><span>Email:<br>info@velora.io</span></div>
    <div class="contact-row"><svg viewBox="0 0 8 8"><path d="M1 1.5l2-.8 1 2-1 .8a4 4 0 0 0 1.6 1.6l.8-1 2 1-.8 2C3.5 7 1 4.5 1 1.5z" fill="var(--orange)"/></svg><span>Phone:<br>08 555-014-2210</span></div>
    <div class="contact-row"><svg viewBox="0 0 8 8"><path d="M4 .5a2.6 2.6 0 0 1 2.6 2.6C6.6 5 4 7.5 4 7.5S1.4 5 1.4 3.1A2.6 2.6 0 0 1 4 .5z" fill="var(--orange)"/></svg><span>Location:<br>Some address line goes<br>here city name country</span></div>
  </div>
  <p class="copy" style="top:1462px">© Copyright 2022 velora, All Rights Reserved</p>
  <div class="to-top" style="left:477px;top:1442px"><svg width="6" height="6" viewBox="0 0 6 6"><path d="M3 5V1M1 3l2-2 2 2" stroke="#fff" fill="none" stroke-width=".8"/></svg></div>
</section>

</body>
</html>
```